stationary deign for trucking company

im a trucking company looking for a professional set of stationary designs i deliver goods from point a to b
Updates

When submitting stationary designs I need envelope design, letterhead, cards, I’d badge etc

Industry/Entity Type

Trucking Company

Requirements
Must have
• must have letter head, business card, envelope, fax sheet, id badge, folder, thank you card, notebook, invoice sheet.
Nice to have
• nice to have them all custom made (letterhead,envelope, business card, I’d badge etc
Should not have
• must not have prepaid sign want i unique design for items

```html
<!DOCTYPE html>
<html lang="en">
<head>
<meta charset="utf-8">
<title>Harlow Transportation Stationery Set</title>
<link href="https://fonts.googleapis.com/css2?family=Montserrat:wght@500;600&family=Roboto:wght@400;500&family=Great+Vibes&family=Open+Sans:wght@600&family=Noto+Serif:wght@400;600&display=swap" rel="stylesheet">
<style>
:root{
  --bg:#d9d9d9;
  --blue:#0a55a4;
  --ink:#1b1b1b;
  --paper:#ffffff;
  --grey:#7a7a7a;
  --rule:#c9c9c9;
  --cell:#e6e6e6;
}
*{box-sizing:border-box;margin:0;padding:0}
html,body{width:1200px;height:923px;overflow:hidden;background:var(--bg)}
body{position:relative;font-family:Roboto,Arial,sans-serif;color:var(--ink)}
.item{position:absolute;background:var(--paper);overflow:hidden;box-shadow:0 1px 3px rgba(0,0,0,.18)}
.blue{background:var(--blue);color:#fff}
.label{position:absolute;font-family:"Open Sans",Arial,sans-serif;font-weight:600;font-size:8.5px;color:#222;text-align:center}
.label.serif{font-family:"Noto Serif",Georgia,serif}

/* brand lockup */
.brand{position:absolute;display:flex;align-items:center;gap:calc(var(--s)*.5)}
.brand .mark{width:var(--s);height:var(--s);border:1.5px solid currentColor;flex:none}
.brand .name{font-family:Montserrat,Arial,sans-serif;font-weight:600;font-size:var(--s);letter-spacing:.14em;line-height:1}
.brand .tag{font-family:Montserrat,Arial,sans-serif;font-weight:500;font-size:calc(var(--s)*.3);letter-spacing:.2em;margin-top:2px;color:var(--grey)}
.blue .brand .tag{color:#fff}

/* footer band */
.footer{position:absolute;left:0;right:0;bottom:0;height:10px}
.footer .line{position:absolute;left:0;right:0;bottom:2px;height:2px;background:var(--ink)}
.footer .line2{position:absolute;left:0;right:0;bottom:0;height:2px;background:var(--blue)}
.footer .tab{position:absolute;right:0;bottom:0;height:10px;width:38%;background:var(--blue);clip-path:polygon(10% 0,100% 0,100% 100%,0 100%);color:#fff;font-size:5px;display:flex;align-items:center;justify-content:center;padding-left:6%}

.contact{position:absolute;font-size:4.2px;line-height:1.45;color:#444;border-left:.5px solid #999;padding-left:6px}
.contact i{display:inline-block;width:3.5px;height:3.5px;background:var(--blue);margin-right:3px;vertical-align:middle}

.pen{position:absolute;left:1128px;top:200px;width:24px;height:232px;border-radius:10px 10px 4px 4px;background:linear-gradient(90deg,#3a3a3a,#8a8a8a 40%,#2c2c2c)}

/* notebook */
.rings{position:absolute;left:-2px;top:12px;bottom:14px;width:8px;background:repeating-linear-gradient(180deg,#555 0 1px,transparent 1px 4px)}
.lines{position:absolute;left:21px;right:25px;top:75px}
.lines div{height:15.6px;border-bottom:.6px solid var(--rule)}

/* fax */
.fax-grid{position:absolute;left:22px;top:81px;width:214px;display:grid;grid-template-columns:30px 76px 30px 76px;gap:1px;font-size:3.6px;color:#555}
.fax-grid span{background:var(--cell);height:10px;padding:3px 3px}
.checks{position:absolute;left:22px;top:133px;display:flex;gap:15px;font-size:3.2px;color:#555}
.checks b{display:inline-block;width:4px;height:4px;border:.5px solid #555;margin-right:2px;vertical-align:middle}

/* invoice */
.inv{position:absolute;left:24px;top:133px;width:208px;border:.8px solid #333;border-top:none}
.inv .head{display:grid;grid-template-columns:18px 1fr 28px 27px;background:#2b2b2b;color:#fff;font-size:3.4px;height:8px;align-items:center;text-align:center}
.inv .row{height:9px;display:grid;grid-template-columns:18px 1fr 28px 27px}
.inv .row:nth-child(odd){background:var(--cell)}
.inv .row span{border-right:.6px solid #333}
.inv .row span:last-child{border-right:none}
.small{font-size:3.6px;color:#444;position:absolute}
.uline{display:inline-block;border-bottom:.5px solid #444}
</style>
</head>
<body>

<!-- business card front -->
<section class="item" style="left:49px;top:78px;width:118px;height:70px">
  <div class="brand" style="--s:6px;left:59px;top:9px;color:var(--ink)">
    <span class="mark"></span><div><div class="name">HARLOW</div><div class="tag">TRANSPORT · LOGISTICS</div></div>
  </div>
  <div style="position:absolute;left:7px;top:32px;font-size:4.5px;font-weight:500;color:var(--blue)">MARK ELLISON</div>
  <div class="small" style="left:7px;top:37px;font-size:2.8px">CEO / FOUNDER</div>
  <div class="small" style="left:7px;top:44px;font-size:2.8px;line-height:1.5">555 210 4871<br>555 388 1902<br>555 674 3025<br>mark@harlowfreight.com</div>
  <div class="small" style="left:74px;top:50px;font-size:2.6px;line-height:1.5">1420 Cedar Ridge Road<br>Fairbanks, Alaska 99701</div>
  <div class="footer" style="height:6px"><div class="line"></div><div class="line2"></div><div class="tab" style="height:6px;font-size:3px">www.harlowfreight.com</div></div>
</section>
<div class="label" style="left:49px;top:156px;width:118px">Front Card</div>

<!-- business card back -->
<section class="item blue" style="left:182px;top:78px;width:122px;height:70px">
  <div style="position:absolute;left:51px;top:20px;width:20px;height:20px;border:1.5px solid #fff"></div>
  <div style="position:absolute;left:0;right:0;top:59px;text-align:center;font-size:3.2px;letter-spacing:.3em">www.harlowfreight.com</div>
</section>
<div class="label" style="left:182px;top:156px;width:122px">Back Card</div>

<!-- envelope back -->
<section class="item" style="left:48px;top:177px;width:257px;height:116px">
  <svg width="257" height="45" style="position:absolute;left:0;top:0" aria-hidden="true"><path d="M0 0H257L250 34Q248 42 238 42H17Q7 42 5 34Z" fill="var(--blue)"/></svg>
  <div style="position:absolute;left:121px;top:12px;width:16px;height:16px;border:1.5px solid #fff"></div>
</section>
<div class="label" style="left:48px;top:302px;width:257px">Envelope Back</div>

<!-- envelope front -->
<section class="item" style="left:48px;top:322px;width:257px;height:116px">
  <div class="brand" style="--s:8.5px;left:17px;top:20px;color:var(--ink)">
    <span class="mark"></span><div><div class="name">HARLOW</div><div class="tag">TRANSPORTATION · LOGISTICS</div></div>
  </div>
  <div class="small" style="left:16px;top:41px;font-size:5px;line-height:1.25">1420 Cedar Ridge Road<br>Fairbanks, Alaska 99701</div>
  <div class="footer"><div class="line"></div><div class="line2"></div><div class="tab">www.harlowfreight.com</div></div>
</section>
<div class="label" style="left:48px;top:446px;width:257px">Envelope Front</div>

<!-- notebook -->
<section class="item" style="left:354px;top:84px;width:275px;height:355px">
  <div class="rings"></div>
  <div class="brand" style="--s:10px;left:86px;top:21px;color:var(--ink)">
    <span class="mark"></span><div><div class="name">HARLOW</div><div class="tag">TRANSPORTATION · LOGISTICS</div></div>
  </div>
  <div class="lines">
    <div></div><div></div><div></div><div></div><div></div><div></div><div></div><div></div><div></div><div></div><div></div><div></div><div></div><div></div><div></div><div></div><div></div><div></div><div></div><div></div>
  </div>
  <div class="footer"><div class="line"></div><div class="line2"></div><div class="tab">www.harlowfreight.com</div></div>
</section>
<div class="label serif" style="left:354px;top:450px;width:275px">Notebook</div>

<!-- thank you front -->
<section class="item" style="left:680px;top:90px;width:216px;height:158px">
  <div class="brand" style="--s:14px;left:30px;top:30px;color:var(--ink)">
    <span class="mark"></span><div><div class="name">HARLOW</div><div class="tag">TRANSPORTATION · LOGISTICS</div></div>
  </div>
  <div style="position:absolute;left:40px;top:80px;font-family:'Great Vibes',cursive;font-size:30px;color:var(--blue)">Thank you</div>
  <div class="footer"><div class="line"></div><div class="line2"></div><div class="tab">www.harlowfreight.com</div></div>
</section>
<div style="position:absolute;left:896px;top:90px;width:16px;height:148px;background:var(--blue);clip-path:polygon(0 0,100% 100%,0 100%)"></div>
<div class="label" style="left:680px;top:257px;width:216px">Thank You Card_Front</div>

<!-- thank you back -->
<section class="item blue" style="left:677px;top:277px;width:216px;height:159px">
  <div style="position:absolute;left:0;right:0;top:126px;text-align:center;font-size:5.2px;line-height:1.4">1420 Cedar Ridge Road, Fairbanks, Alaska 99701<br>P: 555 210 4871 &nbsp;M: 555 388 1902 &nbsp;F: 555 674 3025<br>E: mark@harlowfreight.com &nbsp;W: harlowfreight.com</div>
</section>
<div class="label serif" style="left:677px;top:442px;width:216px">Thank You Card_Back</div>

<!-- id badge -->
<section class="item" style="left:946px;top:210px;width:146px;height:226px;background:#f7f7f7">
  <div class="brand" style="--s:12px;left:12px;top:22px;color:var(--ink)">
    <span class="mark"></span><div><div class="name">HARLOW</div><div class="tag">TRANSPORTATION · LOGISTICS</div></div>
  </div>
  <div style="position:absolute;left:0;right:0;top:90px;text-align:center;font-family:'Noto Serif',serif;font-size:9px;color:#555">Staff I.D. CARD</div>
  <div role="img" aria-label="Staff photo placeholder" style="position:absolute;left:23px;top:125px;width:44px;height:54px;border-radius:4px;background:#a8a8a8"></div>
  <div class="small" style="left:78px;top:125px;font-size:6.5px;line-height:1.55;color:#777">Your Name<br>Position<br>Date of birth<br>Sex<br>Blood group<br>Valid up to :</div>
  <div class="small" style="left:10px;top:210px;font-size:4.6px;color:#777">Card holder signature</div>
  <div class="small" style="left:82px;top:210px;font-size:4.6px;color:#777">Authorised signature</div>
</section>
<div class="label serif" style="left:946px;top:444px;width:146px">id badge</div>
<div class="pen" role="img" aria-label="Ballpoint pen"></div>

<!-- letterhead -->
<section class="item" style="left:50px;top:471px;width:256px;height:364px">
  <div class="brand" style="--s:8px;left:26px;top:42px;color:var(--ink)">
    <span class="mark"></span><div><div class="name">HARLOW</div><div class="tag">TRANSPORTATION · LOGISTICS</div></div>
  </div>
  <div class="contact" style="left:168px;top:27px">1420 Cedar Ridge Road<br>Fairbanks, Alaska 99701<br><i></i>555 210 4871<br><i></i>555 388 1902<br><i></i>555 674 3025<br><i></i>mark@harlowfreight.com</div>
  <div class="footer"><div class="line"></div><div class="line2"></div><div class="tab">www.harlowfreight.com</div></div>
</section>
<div class="label" style="left:50px;top:846px;width:256px">Letterhead A4</div>

<!-- folder -->
<section class="item blue" style="left:337px;top:471px;width:257px;height:364px">
  <div class="brand" style="--s:17px;left:50px;top:145px;color:#fff">
    <span class="mark" style="width:24px;height:24px"></span><div><div class="name">HARLOW</div><div class="tag">TRANSPORTATION · LOGISTICS</div></div>
  </div>
  <div style="position:absolute;left:0;right:0;top:323px;text-align:center;font-size:8.5px">www.harlowfreight.com</div>
</section>
<div class="label" style="left:337px;top:846px;width:257px">Folder A4</div>

<!-- fax -->
<section class="item" style="left:618px;top:471px;width:256px;height:364px">
  <div class="brand" style="--s:8px;left:26px;top:36px;color:var(--ink)">
    <span class="mark"></span><div><div class="name">HARLOW</div><div class="tag">TRANSPORTATION · LOGISTICS</div></div>
  </div>
  <div class="contact" style="left:170px;top:22px">1420 Cedar Ridge Road<br>Fairbanks, Alaska 99701<br><i></i>555 210 4871<br><i></i>555 388 1902<br><i></i>555 674 3025<br><i></i>mark@harlowfreight.com</div>
  <div class="fax-grid">
    <span>To</span><span></span><span>From</span><span></span>
    <span>Fax</span><span></span><span>Pages</span><span></span>
    <span>Phone</span><span></span><span>Date</span><span></span>
    <span>Re</span><span></span><span>CC</span><span></span>
  </div>
  <div class="checks"><span><b></b>Urgent</span><span><b></b>For Review</span><span><b></b>Please comment</span><span><b></b>Please reply</span><span><b></b>Please recycle</span></div>
  <div class="small" style="left:24px;top:145px;font-size:4px">Comments :</div>
  <div class="footer"><div class="line"></div><div class="line2"></div><div class="tab">www.harlowfreight.com</div></div>
</section>
<div class="label" style="left:618px;top:846px;width:256px">Fax A4</div>

<!-- invoice -->
<section class="item" style="left:902px;top:471px;width:256px;height:364px">
  <div class="brand" style="--s:8px;left:26px;top:36px;color:var(--ink)">
    <span class="mark"></span><div><div class="name">HARLOW</div><div class="tag">TRANSPORTATION · LOGISTICS</div></div>
  </div>
  <div class="contact" style="left:170px;top:22px">1420 Cedar Ridge Road<br>Fairbanks, Alaska 99701<br><i></i>555 210 4871<br><i></i>555 388 1902<br><i></i>555 674 3025<br><i></i>mark@harlowfreight.com</div>
  <div class="small" style="left:24px;top:92px">INVOICE # :</div>
  <div class="small" style="left:180px;top:92px">DATE :</div>
  <div class="small" style="left:24px;top:101px">Customer : <span class="uline" style="width:185px"></span></div>
  <div class="small" style="left:24px;top:109px">Address :</div>
  <div class="small" style="left:24px;top:117px">Phone : <span class="uline" style="width:90px"></span> &nbsp;Fax : <span class="uline" style="width:80px"></span></div>
  <div class="inv">
    <div class="head"><span>QTY</span><span>DESCRIPTION</span><span>PRICE</span><span>AMOUNT</span></div>
    <div class="row"><span></span><span></span><span></span><span></span></div>
    <div class="row"><span></span><span></span><span></span><span></span></div>
    <div class="row"><span></span><span></span><span></span><span></span></div>
    <div class="row"><span></span><span></span><span></span><span></span></div>
    <div class="row"><span></span><span></span><span></span><span></span></div>
    <div class="row"><span></span><span></span><span></span><span></span></div>
    <div class="row"><span></span><span></span><span></span><span></span></div>
    <div class="row"><span></span><span></span><span></span><span></span></div>
    <div class="row"><span></span><span></span><span></span><span></span></div>
    <div class="row"><span></span><span></span><span></span><span></span></div>
    <div class="row"><span></span><span></span><span></span><span></span></div>
    <div class="row"><span></span><span></span><span></span><span></span></div>
    <div class="row"><span></span><span></span><span></span><span></span></div>
    <div class="row"><span></span><span></span><span></span><span></span></div>
    <div class="row"><span></span><span></span><span></span><span></span></div>
    <div class="row"><span></span><span></span><span></span><span></span></div>
    <div class="row"><span></span><span></span><span></span><span></span></div>
    <div class="row"><span></span><span></span><span></span><span></span></div>
    <div class="row"><span></span><span></span><span></span><span></span></div>
  </div>
  <div class="checks" style="left:24px;top:285px;gap:10px"><span><b></b>CARD</span><span><b></b>CHECK</span><span><b></b>DEBIT</span><span><b></b>CASH</span><span><b></b>CHEQUE</span></div>
  <div style="position:absolute;left:178px;top:280px;width:54px;font-size:3.2px;font-weight:500">
    <div style="display:grid;grid-template-columns:27px 27px;border:.6px solid #333;height:9px;align-items:center;padding-left:2px">SUB TOTAL<span></span></div>
    <div style="display:grid;grid-template-columns:27px 27px;border:.6px solid #333;border-top:none;height:9px;align-items:center;padding-left:2px">TAX #<span></span></div>
    <div style="display:grid;grid-template-columns:27px 27px;border:.6px solid #333;border-top:none;height:9px;align-items:center;padding-left:2px">TOTAL<span></span></div>
  </div>
  <div class="small" style="left:24px;top:301px;font-size:2.8px;line-height:1.4">Signature indicates<br>Acceptance of Price and terms</div>
  <div class="footer"><div class="line"></div><div class="line2"></div><div class="tab">www.harlowfreight.com</div></div>
</section>
<div class="label" style="left:902px;top:846px;width:256px">Invoice A4</div>

</body>
</html>
```